Kestal-Materials. Limestone; improving the world

New Limestone company and need logo design.
Limestone offsets carbon mitigation industries restore and replenish soil fertilities in the Prairies, the breadbasket of the world. At the same time, Limestone is proving a critical emergent component of carbon capture sequestration technology will therefore play a critical role in the development of the western Canadian energy industries
Our limestone resources are situated in the foothills of the Canadian Rockies well-positioned above the sprawling fields of the vast peace district.
Agriculture and oli sites
Kestal Materials
3 page

```html
<!DOCTYPE html>
<html lang="en">
<head>
<meta charset="utf-8">
<title>Kestal Materials</title>
<link href="https://fonts.googleapis.com/css2?family=Arimo:wght@400;700&family=Lato:wght@400;700&family=Roboto:wght@300;400;500;700&display=swap" rel="stylesheet">
<style>
:root{
  --green:#4fa800;
  --blue:#2aa7f2;
  --slate:#4a6f8c;
  --dark:#1c1c1c;
  --ink:#222;
  --muted:#666;
  --white:#fff;
}
*{margin:0;padding:0;box-sizing:border-box}
html,body{width:1200px;height:3315px;overflow:hidden;background:var(--white)}
body{position:relative;font-family:'Roboto',sans-serif;color:var(--ink)}
.abs{position:absolute}
.hero-photo{left:0;top:0;width:1200px;height:640px;background:radial-gradient(circle at 470px 260px,#6c8f2a 0,#3c5a1a 30%,#1f2d12 65%,#141d0d 100%)}
.brand{left:142px;top:32px;font-family:'Arimo',sans-serif;font-weight:700;font-variant:small-caps;font-size:30px;color:var(--white);letter-spacing:.5px}
.nav{left:519px;top:47px;display:flex;gap:0;font-family:'Roboto',sans-serif;font-weight:700;font-size:13px;color:var(--white)}
.nav a{color:var(--white);text-decoration:none;position:absolute;white-space:nowrap}
.nav a.active{color:var(--green)}
.hero-title{left:604px;top:180px;font-family:'Arimo',sans-serif;font-weight:700;font-size:56px;line-height:47px;color:var(--white)}
.btn{display:flex;align-items:center;justify-content:center;gap:4px;background:var(--blue);color:var(--white);border-radius:24px;font-family:'Roboto',sans-serif;font-weight:700;font-size:12px;letter-spacing:-.2px}
.btn .dot{width:11px;height:11px;border-radius:50%;background:var(--white);display:inline-flex;align-items:center;justify-content:center}
.arrow{width:47px;height:47px;border-radius:50%;background:rgba(255,255,255,.35);display:flex;align-items:center;justify-content:center}
.green-band{left:0;top:620px;width:1200px;height:575px;background:var(--green)}
.h2-white{font-family:'Arimo',sans-serif;font-weight:700;font-size:36px;color:var(--white)}
.copy-white{font-family:'Lato',sans-serif;font-size:11.6px;line-height:21px;color:var(--white);text-align:justify}
.quarry-photo{left:646px;top:657px;width:410px;height:440px;border-radius:4px;background:linear-gradient(180deg,#6b9ac8 0,#c9b28a 45%,#d89a45 60%,#5a5650 75%,#7a7670 100%)}
.quarry-frame{left:671px;top:633px;width:408px;height:438px;border:4px solid var(--white);border-radius:4px}
.center-title{left:0;width:1200px;text-align:center;font-family:'Arimo',sans-serif;font-weight:700}
.copy-grey{font-family:'Lato',sans-serif;font-size:12.5px;line-height:21px;color:var(--muted);text-align:center}
.feature{width:136px;height:136px;border-radius:50%;display:flex;align-items:center;justify-content:center}
.feature-label{width:220px;text-align:center;font-family:'Roboto',sans-serif;font-weight:300;font-size:20px;color:#555}
.mission-photo{left:0;top:1714px;width:1200px;height:420px;background:linear-gradient(100deg,#d89a4a 0,#8ba83a 30%,#3f6a22 55%,#3a2d22 80%,#2a2018 100%)}
.play{left:141px;top:1926px;width:106px;height:106px;border-radius:50%;border:3px solid rgba(255,255,255,.85);background:rgba(255,255,255,.35);display:flex;align-items:center;justify-content:center}
.blog-lead{left:151px;top:2289px;width:419px;height:358px;background:linear-gradient(180deg,#5a5040 0,#d8cfc2 35%,#efe9e1 65%,#c9b49a 100%)}
.blog-lead-card{left:227px;top:2478px;width:343px;height:169px;background:rgba(255,255,255,.88);padding:24px 0 0 25px}
.blog-title{font-family:'Roboto',sans-serif;font-weight:500;font-size:17px;line-height:22px;color:var(--ink)}
.meta{font-family:'Roboto',sans-serif;font-size:12px;color:var(--green);display:flex;align-items:center;gap:6px}
.excerpt{font-family:'Roboto',sans-serif;font-size:13px;line-height:20px;color:#555}
.blog-card{left:605px;width:445px;height:168px;border:1px solid #e3e3e3;background:var(--white)}
.blog-card .thumb{position:absolute;left:0;top:0;width:186px;height:100%}
.blog-card .body{position:absolute;left:210px;top:20px;width:225px}
.footer{left:0;top:2830px;width:1200px;height:485px;background:var(--dark)}
.f-head{font-family:'Roboto',sans-serif;font-weight:500;font-size:17px;color:var(--white)}
.field{background:var(--white);border:1px solid #ccc;font-family:'Roboto',sans-serif;font-size:12px;color:#666;padding:10px 16px}
.submit{left:143px;top:3153px;width:125px;height:43px;border-radius:22px;background:var(--green);color:var(--white);font-weight:700;font-size:14px;display:flex;align-items:center;justify-content:center}
.link{font-family:'Roboto',sans-serif;font-size:14px;color:var(--white);display:flex;align-items:center;gap:10px}
.contact-row{font-family:'Roboto',sans-serif;font-size:14px;line-height:21px;color:var(--white)}
.rule{left:143px;top:3229px;width:912px;height:1px;background:#444}
.legal{left:0;top:3259px;width:1200px;text-align:center;font-family:'Roboto',sans-serif;font-size:14px;color:var(--white)}
</style>
</head>
<body>

<header>
  <div class="abs hero-photo" role="img" aria-label="Hands cupping soil with a young green seedling against a soft green background"></div>
  <div class="abs brand">Kestal Materials</div>
  <nav class="abs nav">
    <a class="active" style="left:0;top:0">HOME</a>
    <a style="left:67px;top:0">ABOUT US</a>
    <a style="left:162px;top:0">SERVICES</a>
    <a style="left:255px;top:0">BLOG</a>
    <a style="left:321px;top:0">SUSTAINABILITY</a>
    <a style="left:453px;top:0">CONTACT US</a>
  </nav>
  <h1 class="abs hero-title">WE ARE A<br>NEW LIMESTONE<br>COMPANY</h1>
  <div class="abs btn" style="left:604px;top:342px;width:144px;height:43px">LEARN MORE <span class="dot"><svg width="7" height="7" viewBox="0 0 8 8"><path d="M2 1l3 3-3 3" stroke="#2aa7f2" stroke-width="1.6" fill="none"/></svg></span></div>
  <div class="abs arrow" style="left:49px;top:282px"><svg width="12" height="14" viewBox="0 0 12 14"><path d="M8 2L3 7l5 5" stroke="#fff" stroke-width="2" fill="none"/></svg></div>
  <div class="abs arrow" style="left:1105px;top:282px"><svg width="12" height="14" viewBox="0 0 12 14"><path d="M4 2l5 5-5 5" stroke="#fff" stroke-width="2" fill="none"/></svg></div>
</header>

<section class="who">
  <svg class="abs" style="left:0;top:490px" width="1200" height="140" viewBox="0 0 1200 140"><path d="M0 140 L0 140 C200 145 380 110 560 55 C740 0 960 -10 1200 25 L1200 140 Z" fill="#4fa800"/></svg>
  <div class="abs green-band"></div>
  <svg class="abs" style="left:0;top:1130px" width="1200" height="65" viewBox="0 0 1200 65"><path d="M0 65 L0 35 C20 20 40 40 55 28 C70 15 90 30 110 22 C130 12 150 30 170 30 C190 32 205 5 230 10 C260 14 270 -2 300 5 C320 10 330 2 350 12 C370 20 380 30 390 40 C400 55 395 25 420 22 C450 18 470 40 490 30 C510 20 530 35 545 30 C560 20 575 35 600 25 C620 18 630 35 655 28 C670 22 680 0 700 4 C720 8 735 -2 760 6 C780 12 800 10 820 22 C840 35 860 25 880 30 C900 38 920 20 945 28 C970 35 980 18 1000 22 C1020 28 1040 10 1060 15 C1080 20 1100 35 1120 30 C1140 25 1160 10 1180 5 L1200 0 L1200 65 Z" fill="#fff"/></svg>
  <h2 class="abs h2-white" style="left:142px;top:705px">WHO WE ARE</h2>
  <p class="abs copy-white" style="left:142px;top:760px;width:434px">Lorem ipsum dolor sit amet, consectetur adipiscing elit, sed do eiusmod tempor incididunt ut labore et dolore magna aliqua. Ut enim ad minim veniam, quis nostrud exercitation ullamco laboris nisi ut aliquip ex ea commodo consequat. Duis aute irure dolor in reprehenderit in voluptate velit esse cillum dolore eu fugiat nulla pariatur. Excepteur sint occaecat cupidatat non proident, sunt in culpa qui officia deserunt mollit anim id est laborum.</p>
  <p class="abs copy-white" style="left:142px;top:905px;width:434px">Lorem ipsum dolor sit amet, consectetur adipiscing elit, sed do eiusmod tempor incididunt ut labore et dolore magna aliqua. Ut enim ad minim veniam, quis nostrud exercitation ullamco laboris nisi ut aliquip ex ea commodo consequat. Duis aute irure dolor in reprehenderit in voluptate velit esse cillum dolore eu fugiat nulla pariatur. Excepteur sint occaecat cupidatat non proident, sunt in culpa qui officia deserunt mollit anim id est laborum.</p>
  <div class="abs btn" style="left:143px;top:1053px;width:145px;height:43px">LEARN MORE <span class="dot"><svg width="7" height="7" viewBox="0 0 8 8"><path d="M2 1l3 3-3 3" stroke="#2aa7f2" stroke-width="1.6" fill="none"/></svg></span></div>
  <div class="abs quarry-frame"></div>
  <div class="abs quarry-photo" role="img" aria-label="Excavator on a pile of crushed limestone at sunset"></div>
</section>

<section class="world">
  <h2 class="abs center-title" style="top:1278px;font-size:36px;color:var(--slate)">WORLD-CLASS IN EVERYTHING WE DO!</h2>
  <p class="abs copy-grey" style="left:216px;top:1335px;width:763px">Lorem ipsum dolor sit amet, consectetur adipiscing elit, sed do eiusmod tempor incididunt ut labore et dolore magna aliqua. Ut enim ad minim veniam, quis nostrud exercitation ullamco laboris nisi ut aliquip ex ea commodo consequat. Duis aute irure dolor in reprehenderit in voluptate velit esse cillum dolore eu fugiat nulla pariatur. Excepteur sint occaecat cupidatat non proident, sunt in culpa qui officia deserunt mollit anim id est laborum.</p>
  <svg class="abs" style="left:320px;top:1485px" width="570" height="70" viewBox="0 0 570 70"><g stroke="#999" stroke-width="1.2" fill="none" stroke-dasharray="3 3"><path d="M0 60 C30 60 40 8 95 10"/><path d="M230 10 C280 5 290 60 330 60"/><path d="M455 60 C490 60 500 5 550 12"/></g></svg>
  <div class="abs feature" style="left:190px;top:1449px;background:var(--blue)"><svg width="64" height="64" viewBox="0 0 64 64" fill="none" stroke="#fff" stroke-width="2.2"><rect x="8" y="34" width="48" height="20"/><path d="M14 34V20h8v14M26 34V10h10v24M40 34V22h8v12"/><path d="M14 44h36"/></svg></div>
  <div class="abs feature" style="left:417px;top:1449px;background:var(--green)"><svg width="66" height="66" viewBox="0 0 66 66" fill="none" stroke="#fff" stroke-width="2.2"><circle cx="30" cy="36" r="22"/><path d="M16 26c6 2 8 8 14 8s6 8 2 12M38 16c0 6 6 8 10 6"/><path d="M44 18c4-8 12-10 16-10 0 6-4 14-14 14"/></svg></div>
  <div class="abs feature" style="left:645px;top:1449px;background:var(--blue)"><svg width="66" height="66" viewBox="0 0 66 66" fill="none" stroke="#fff" stroke-width="2.2"><path d="M6 36l14-16 10 10 10-14 20 20z"/><rect x="6" y="36" width="54" height="18"/><path d="M6 42h54M6 48h54"/></svg></div>
  <div class="abs feature" style="left:873px;top:1449px;background:var(--green)"><svg width="66" height="66" viewBox="0 0 66 66" fill="none" stroke="#fff" stroke-width="2.2"><circle cx="33" cy="33" r="7"/><circle cx="33" cy="33" r="13" stroke-dasharray="5 3"/><path d="M12 24a22 22 0 0 1 30-14M54 42a22 22 0 0 1-30 14M14 44a22 22 0 0 1-4-12M52 22a22 22 0 0 1 4 12"/><path d="M40 6l3 5-5 2M26 60l-3-5 5-2"/></svg></div>
  <div class="abs feature-label" style="left:148px;top:1596px">Duis aute irure dolor</div>
  <div class="abs feature-label" style="left:375px;top:1596px">Duis aute irure dolor</div>
  <div class="abs feature-label" style="left:603px;top:1596px">Duis aute irure dolor</div>
  <div class="abs feature-label" style="left:831px;top:1596px">Duis aute irure dolor</div>
</section>

<section class="mission">
  <div class="abs mission-photo" role="img" aria-label="Hands holding soil with a green sprout in warm sunlight"></div>
  <h2 class="abs h2-white" style="left:142px;top:1818px;font-size:38px">MISSION</h2>
  <p class="abs" style="left:142px;top:1868px;width:460px;font-family:'Arimo',sans-serif;font-size:12.5px;line-height:21px;color:var(--white)">Lorem ipsum dolor sit amet, consectetur adipiscing elit, sed do eiusmod tempor incididunt ut labore et dolore magna aliqua.</p>
  <div class="abs play"><svg width="34" height="34" viewBox="0 0 34 34"><path d="M9 5l20 12-20 12z" fill="#fff"/></svg></div>
</section>

<section class="blog">
  <h2 class="abs center-title" style="top:2222px;font-size:34px;color:var(--slate)">OUR LATEST BLOG</h2>
  <div class="abs blog-lead" role="img" aria-label="White limestone quarry wall with an excavator"></div>
  <article class="abs blog-lead-card">
    <h3 class="blog-title">Lorem ipsum dolor sit amet,<br>consectetur adipiscing</h3>
    <div class="meta" style="margin-top:14px">▦ 1 April 2020 &nbsp;| &nbsp;● 2 Comments</div>
    <p class="excerpt" style="margin-top:14px;width:310px">Sed ut perspiciatis unde omnis iste natus error sit voluptatem accusantium doloremque</p>
  </article>
  <article class="abs blog-card" style="top:2289px">
    <div class="thumb" role="img" aria-label="Piles of white limestone rock in a quarry" style="background:linear-gradient(180deg,#8a8170 0,#cfc8bc 40%,#e6e1d8 100%)"></div>
    <div class="body">
      <h3 class="blog-title" style="font-size:16px">Lorem ipsum dolor sit amet</h3>
      <div class="meta" style="margin-top:12px">▦ 4th Feby 2020 &nbsp;| &nbsp;● 2 Comments</div>
      <p class="excerpt" style="margin-top:12px">Sed ut perspiciatis unde omnis iste natus voluptatem accusantium doloremque laudantium,</p>
    </div>
  </article>
  <article class="abs blog-card" style="top:2478px">
    <div class="thumb" role="img" aria-label="Conveyor belt over a pile of crushed stone under blue sky" style="background:linear-gradient(180deg,#2f6aa8 0,#7fa6c8 45%,#c9c6c0 70%,#a7a39b 100%)"></div>
    <div class="body">
      <h3 class="blog-title" style="font-size:16px">Lorem ipsum dolor sit amet</h3>
      <div class="meta" style="margin-top:12px">▦ 24th Jany 2020 &nbsp;| &nbsp;● 2 Comments</div>
      <p class="excerpt" style="margin-top:12px">Sed ut perspiciatis unde omnis iste natus voluptatem accusantium doloremque laudantium,</p>
    </div>
  </article>
</section>

<footer>
  <svg class="abs" style="left:0;top:2715px" width="1200" height="120" viewBox="0 0 1200 120"><path d="M0 5 C150 -5 250 40 420 40 C600 40 800 0 1000 5 C1100 8 1160 20 1200 25 L1200 120 L0 120Z" fill="#d9d9d9"/><path d="M0 50 C200 100 400 80 600 50 C800 20 1000 20 1200 60 L1200 120 L0 120Z" fill="#efefef"/><path d="M0 75 C200 130 420 120 640 75 C860 35 1050 40 1200 80 L1200 120 L0 120Z" fill="#1c1c1c"/></svg>
  <div class="abs footer"></div>
  <h4 class="abs f-head" style="left:143px;top:2930px">GET IN TOUCH</h4>
  <div class="abs field" style="left:143px;top:2974px;width:220px;height:37px">First Name</div>
  <div class="abs field" style="left:371px;top:2974px;width:218px;height:37px">Last Name</div>
  <div class="abs field" style="left:143px;top:3020px;width:220px;height:37px">Email</div>
  <div class="abs field" style="left:371px;top:3020px;width:218px;height:37px">phone number</div>
  <div class="abs field" style="left:143px;top:3067px;width:446px;height:70px">Message</div>
  <div class="abs submit">SUBMIT</div>

  <h4 class="abs f-head" style="left:646px;top:2930px">QUICK LINKS</h4>
  <div class="abs link" style="left:646px;top:2966px">» <span>Home</span></div>
  <div class="abs link" style="left:646px;top:2994px">» <span>About Us</span></div>
  <div class="abs link" style="left:646px;top:3022px">» <span>Services</span></div>
  <div class="abs link" style="left:646px;top:3050px">» <span>Contact Us</span></div>
  <div class="abs link" style="left:646px;top:3078px">» <span>Privacy policy</span></div>

  <h4 class="abs f-head" style="left:830px;top:2930px">CONTACT US</h4>
  <div class="abs contact-row" style="left:834px;top:2970px;display:flex;gap:12px"><svg width="10" height="14" viewBox="0 0 10 14"><path d="M5 0a5 5 0 0 1 5 5c0 4-5 9-5 9S0 9 0 5a5 5 0 0 1 5-5z" fill="#fff"/><circle cx="5" cy="5" r="2" fill="#1c1c1c"/></svg><span>270 Lorem ipsum dolor amet,<br>consectetur elit,</span></div>
  <div class="abs contact-row" style="left:834px;top:3027px;display:flex;gap:16px;align-items:center"><svg width="8" height="14" viewBox="0 0 8 14"><rect x="1" y="1" width="6" height="12" rx="1" stroke="#fff" stroke-width="1.4" fill="none"/></svg><span>(555) 014-2280</span></div>
  <div class="abs contact-row" style="left:832px;top:3059px;display:flex;gap:14px;align-items:center"><svg width="14" height="13" viewBox="0 0 14 13"><rect x="1" y="4" width="12" height="8" stroke="#fff" stroke-width="1.4" fill="none"/><rect x="4" y="1" width="6" height="4" stroke="#fff" stroke-width="1.2" fill="none"/></svg><span>123 456 7890</span></div>
  <div class="abs contact-row" style="left:831px;top:3090px;display:flex;gap:12px;align-items:center"><svg width="15" height="11" viewBox="0 0 15 11"><rect x="1" y="1" width="13" height="9" stroke="#fff" stroke-width="1.3" fill="none"/><path d="M1 1l6.5 5L14 1" stroke="#fff" stroke-width="1.3" fill="none"/></svg><span>info@kestalmail.com</span></div>

  <h4 class="abs f-head" style="left:646px;top:3142px">STAY CONNECTED :</h4>
  <div class="abs" style="left:834px;top:3138px;width:30px;height:30px;border-radius:50%;background:#3b5bb8" aria-label="Social profile"></div>
  <div class="abs" style="left:870px;top:3138px;width:30px;height:30px;border-radius:50%;background:#c8309a" aria-label="Social profile"></div>

  <div class="abs rule"></div>
  <p class="abs legal">© 2021 Kestal Materials &nbsp;| All Rights Reserved | Terms and Conditions</p>
</footer>

</body>
</html>
```